New and upgraded www.valdmorefunds.com content & design financial markets

We need an upgrade of our site. The current site is www.valdmorefunds.com
Navigation with full site map i.e. the user can select any page from any menu item.

The “Insights” (Insikter) page will remain as is except new design AND with far more possibilities to add thumbnails, picts, videos etc. The user will have to logon to be able to read the full story.

The “Produkter & Tjänster” (“How to invest” in current web) will contain about the same info as the current “How to invest” pages.

Some pages will contain one or more videos and or speaker supported “live” graphics which we will supply. The media content shall be easy to change.

The site will have two languages from start, English and Swedish. There will be more languages added within 1 year or slightly more.

All texts will be provided by us.

I’m attaching a PDF with suggested content for some of the new pages. However this is just content and absolutely no design. We need new design for the total of the site as well as for the graphics.

Expectation info:
These sites (Both major players in our business) can be used as inspiration:
https://www.tarvenholm.com/eu/en/
https://www.brightwellpartners.com/index.html

Below some opt-OUT and opt-IN graphic rules in connection with the Web supporting our business acumen and brand:

Opt-OUT:
- images similar to educational comic books - it signals an authoritarian approach where the customer is small (insubstantial).
- images that signal trading, cyber, mystery and fast-paced business. We are extremely long-term and invest in real companies
- avoid images containing coins, calculators and banknotes. We're not a savings bank company. or payment service-branch
- avoid images of large data flows, because we should not make facts complex, but simple and comprehensible
- avoid sensing pictures of photo models. We are real people who stand for our efforts. We're not going to hide.
- avoid pictures of suits and tie. They signal rigid-banking. We're smart-investment, flexible, adaptable. Rather curl up your sleeves and show that we’re building something valuable.
- avoid pictures of skyscrapers and cool bank pictures - because they signal the more old valuations of big capital and giant banks - that we are not at all. I know we've had clean facades before. As long as we're not talking about bank skyscrapers, I'm in.

Opt-IN
- pictures of Lukas in moderate amount - he is our symbol person
- films with Lukas and explaining graphical films - explaining and clarifying
- images of pedagogy that give the customer a sense of overview and insights that we give to the customers in our service
- illustrations that explain and deepen our work
- pictures and bars that in 3d illustrate our consistent results and stable delivery
- images that signal that we have a full grasp of data, flows and analyses - without the image becoming a space adventure
- use the logo as a grid, shape and colour.
- no genre portraits, rather pictures of real customers - which gives a sense of why they are customers here
- images that support our core i.e. is science, innovation, unrestricted thinking (“out of the box” – (don’t like that sentence)), smart-solutions, data-driven, client-cantered, flexible and adaptable to client needs and expectation.
- Solid - to be trustworthy in any economic climate
- Long term - consistent work and choices. No trading. Numbers talk
- Data-driven - real tech - combining years of work in finance with straight on tech

Presenting on the webpage:
The story in text and illustration
Show the truth - we have a great history to show and give space
Only numbers and graphs that has a meaning - no artificial numbers etc.
Updates

Target Market(s)

Europe

Coding

Coded - Design and coding required

Number of Pages Required

5+ page

Colors

Designer to choose colors to be used in the design.

Requirements
Must have
• Colours in line with www.valdmorefunds.com

```html
<!DOCTYPE html>
<html lang="en">
<head>
<meta charset="utf-8">
<title>Valdmore Capital – Your Personal Investment Advisor</title>
<link rel="stylesheet" href="https://fonts.googleapis.com/css2?family=Barlow:wght@400;500;600;700&display=swap">
<style>
:root{
  --navy:#16207a;
  --navy-deep:#0c1459;
  --navy-light:#2c3a9e;
  --red:#e0262f;
  --ink:#1f2433;
  --muted:#6b7080;
  --grey-bg:#f2f3f6;
  --line:#d9dbe3;
  --footer:#1b1b1e;
  --white:#ffffff;
}
*{box-sizing:border-box;margin:0;padding:0}
html,body{width:1200px;height:4596px;overflow:hidden}
body{font-family:"Barlow",Arial,sans-serif;color:var(--ink);background:var(--white);position:relative}
.wrap{width:976px;margin:0 auto;position:relative}

/* header */
.site-header{height:112px;display:flex;align-items:center;justify-content:center}
.brand{display:flex;align-items:center;gap:12px;font-size:30px;font-weight:600;color:var(--navy)}
.brand-square{width:26px;height:26px;background:var(--navy)}
.main-nav{height:48px;background:var(--navy)}
.main-nav ul{list-style:none;display:flex;width:976px;margin:0 auto;height:48px}
.main-nav li{font-size:13px;font-weight:500;letter-spacing:.5px;color:var(--white);padding:0 28px;display:flex;align-items:center}
.main-nav li.active{background:var(--navy-light)}

/* hero */
.hero{height:780px;position:relative;clip-path:polygon(0 0,100% 0,100% 86%,50% 100%,0 86%);
  background:linear-gradient(160deg,#6f8fc9 0%,#3f5fa8 35%,#1f3a86 70%,#182c6e 100%);
  display:flex;flex-direction:column;align-items:center;justify-content:center;text-align:center;color:var(--white)}
.hero h1{font-size:92px;font-weight:500;line-height:1;margin-top:-60px}
.hero p{font-size:36px;font-weight:500;letter-spacing:1px;margin-top:22px;text-transform:uppercase}

/* features */
.features{height:360px;display:flex;justify-content:center;gap:40px;padding-top:90px}
.feature{width:240px;text-align:center}
.feature svg.icon{width:52px;height:52px;display:block;margin:0 auto 14px}
.feature h3{font-size:21px;font-weight:600;margin-bottom:12px}
.feature p{font-size:13px;color:var(--muted);line-height:1.5}
.round-arrow{width:30px;height:30px;border:1px solid var(--navy);border-radius:50%;margin:14px auto 0;display:flex;align-items:center;justify-content:center}

/* about */
.about{height:420px;background:var(--grey-bg)}
.about .wrap{display:flex;justify-content:space-between;padding-top:70px}
.about-text{width:420px}
.section-title{font-size:36px;font-weight:600;color:var(--ink);margin-bottom:24px}
.about-text p{font-size:14px;color:var(--muted);line-height:1.6;margin-bottom:18px}
.btn-outline{display:inline-block;border:2px solid var(--navy);color:var(--navy);font-size:14px;font-weight:600;padding:9px 18px}
.about-photo{width:508px;height:240px;margin-top:10px;background:linear-gradient(120deg,#c9d2de,#8592a8 55%,#4e5a72)}

/* approach */
.approach{height:540px;text-align:center;padding-top:60px}
.approach .section-title{margin-bottom:16px}
.approach-intro{font-size:14px;color:var(--muted);width:520px;margin:0 auto;line-height:1.6}
.approach-graphic{position:relative;width:976px;height:320px;margin:30px auto 0}
.approach-graphic svg.arcs{position:absolute;left:0;top:0}
.approach-circle{position:absolute;width:220px;height:220px;border-radius:50%;background:var(--white);box-shadow:0 6px 24px rgba(22,32,122,.14);
  display:flex;flex-direction:column;align-items:center;justify-content:center;padding:0 30px}
.approach-circle h4{font-size:24px;font-weight:500;color:var(--navy);margin-bottom:10px}
.approach-circle p{font-size:12px;color:var(--muted);line-height:1.5}
.c1{left:98px;top:70px}.c2{left:378px;top:20px;border:6px solid #c7ccec}.c3{left:658px;top:70px}

/* philosophy */
.philosophy{height:550px;background:var(--navy)}
.philosophy .wrap{display:flex;justify-content:space-between;padding-top:70px;color:var(--white)}
.eyebrow{font-size:22px;font-weight:500}
.philosophy h2{font-size:40px;font-weight:500;margin-bottom:28px}
.check-list{list-style:none}
.check-list li{font-size:14px;margin-bottom:15px;display:flex;align-items:center;gap:14px}
.philosophy-visual{position:relative;width:408px;height:380px;margin-top:10px}
.philosophy-visual .frame{position:absolute;left:24px;top:24px;right:-16px;bottom:-16px;border:4px solid var(--white)}
.philosophy-visual .img{position:absolute;inset:0;background:linear-gradient(135deg,#e6e8ee,#a9b0c2 50%,#5d6680)}

/* strategy */
.strategy{height:460px}
.strategy .wrap{display:flex;justify-content:space-between;padding-top:60px}
.chart-card{width:496px;height:340px;background:var(--white);box-shadow:0 4px 22px rgba(0,0,0,.12);padding:30px}
.chart-fill{width:100%;height:100%;background:linear-gradient(160deg,#f6e3e5 0%,#eef0f8 50%,#d9dcef 100%)}
.strategy-text{width:420px;padding-top:16px}
.strategy-text .eyebrow{color:var(--ink)}
.strategy-text h2{font-size:34px;font-weight:600;margin-bottom:28px}
.arrow-list{list-style:none}
.arrow-list li{font-size:14px;color:var(--muted);margin-bottom:16px;display:flex;align-items:center;gap:14px}

/* intelligence */
.intelligence{height:520px}
.intelligence .wrap{display:flex;justify-content:space-between;padding-top:60px}
.intel-text{width:500px;padding-top:30px}
.intel-text h2{font-size:34px;font-weight:600;color:var(--navy);margin-bottom:24px}
.intel-text p{font-size:14px;color:var(--muted);line-height:1.6;margin-bottom:16px}
.btn-solid{display:inline-block;background:var(--navy-deep);color:var(--white);font-size:14px;font-weight:600;padding:12px 24px;margin-top:10px}
.phone{width:240px;height:440px;margin-right:80px;border-radius:30px;background:linear-gradient(180deg,#d6d9e2,#9ea4b5 50%,#6b738c)}

/* message */
.message{height:520px;background:linear-gradient(160deg,#2a4aa8,#1b3490 50%,#14257a);text-align:center;color:var(--white);padding-top:60px}
.message h2{font-size:40px;font-weight:600;letter-spacing:1px}
.message-sub{font-size:14px;margin:16px 0 30px;opacity:.9}
.contact-form{width:600px;margin:0 auto;text-align:left}
.form-row{display:flex;gap:16px;margin-bottom:16px}
.field{flex:1;height:40px;background:var(--white);color:var(--muted);font-size:13px;padding:11px 12px}
.field.area{height:100px}
.btn-send{display:block;width:120px;margin:6px auto 0;background:var(--navy-deep);color:var(--white);font-size:14px;font-weight:600;text-align:center;padding:11px 0}

/* footer */
.site-footer{height:286px;background:var(--footer);color:var(--white);text-align:center;padding-top:60px}
.site-footer .brand{color:var(--white);justify-content:center}
.site-footer .brand-square{background:var(--white)}
.footer-nav{list-style:none;display:flex;justify-content:center;gap:40px;margin:40px 0 30px;font-size:13px;font-weight:500}
.copyright{font-size:12px;color:#a8a9b0}
</style>
</head>
<body>

<header class="site-header">
  <div class="brand"><span class="brand-square"></span>Valdmore Capital</div>
</header>
<nav class="main-nav">
  <ul>
    <li class="active">HOME</li><li>PHILOSOPHY</li><li>HOW TO INVEST</li><li>WHAT WE DO</li><li>CONTACT</li><li>INSIGHTS</li><li>CASES</li>
  </ul>
</nav>

<section class="hero" role="img" aria-label="Photograph of a calm city skyline with glass buildings in blue tones">
  <h1>Valdmore Capital</h1>
  <p>Your Personal Investment Advisor</p>
</section>

<section class="features">
  <div class="feature">
    <svg class="icon" viewBox="0 0 52 52" fill="none" stroke="var(--navy)" stroke-width="2.5"><circle cx="26" cy="16" r="9"/><path d="M10 46c0-9 7-15 16-15s16 6 16 15"/></svg>
    <h3>Why Choose Us</h3>
    <p>We secure your interest by continuously keeping your investment updated</p>
    <div class="round-arrow"><svg width="12" height="12" viewBox="0 0 12 12" fill="none" stroke="var(--navy)" stroke-width="1.6"><path d="M4 2l4 4-4 4"/></svg></div>
  </div>
  <div class="feature">
    <svg class="icon" viewBox="0 0 52 52" fill="none" stroke="var(--navy)" stroke-width="2.5"><path d="M8 46h36"/><path d="M14 44V32M22 44V26M30 44V30M38 44V20"/><circle cx="26" cy="11" r="8"/></svg>
    <h3>Investment Intelligence</h3>
    <p>We secure your interest by continuously keeping your investment updated</p>
    <div class="round-arrow"><svg width="12" height="12" viewBox="0 0 12 12" fill="none" stroke="var(--navy)" stroke-width="1.6"><path d="M4 2l4 4-4 4"/></svg></div>
  </div>
  <div class="feature">
    <svg class="icon" viewBox="0 0 52 52" fill="none" stroke="var(--navy)" stroke-width="2.5"><circle cx="26" cy="26" r="18"/><circle cx="26" cy="26" r="10"/><circle cx="26" cy="26" r="3" fill="var(--navy)"/><path d="M26 2v8M26 42v8M2 26h8M42 26h8"/></svg>
    <h3>Client Focus</h3>
    <p>We secure your interest by continuously keeping your investment updated</p>
    <div class="round-arrow"><svg width="12" height="12" viewBox="0 0 12 12" fill="none" stroke="var(--navy)" stroke-width="1.6"><path d="M4 2l4 4-4 4"/></svg></div>
  </div>
</section>

<section class="about">
  <div class="wrap">
    <div class="about-text">
      <h2 class="section-title">About Us</h2>
      <p>We are a privately held firm dedicated to clients who have entrusted us with their wealth. We act calmly and transparently in the best interest of our clients. We pride ourselves on our discretion and confidentiality.</p>
      <p>You can be assured of a single client-centric service, high quality, totally unbiased investment advice. We are the only boutique, i.e. we have no affiliations with any financial institutions – we do not take any commission from product providers – we think only for you!</p>
      <span class="btn-outline">Read More</span>
    </div>
    <div class="about-photo" role="img" aria-label="Portrait photograph of a team member in a bright office"></div>
  </div>
</section>

<section class="approach">
  <h2 class="section-title">Our Approach</h2>
  <p class="approach-intro">Valdmore Capital is truly different – We deliver Investment Services that sets us apart from our contemporaries' approach to the financial markets.</p>
  <div class="approach-graphic">
    <svg class="arcs" width="976" height="320" viewBox="0 0 976 320" fill="none" stroke="var(--navy)" stroke-width="8" stroke-linecap="round">
      <path d="M128 250 A130 130 0 0 1 208 60"/>
      <path d="M420 40 A140 140 0 0 1 556 40" stroke="#8d96d4"/>
      <path d="M848 250 A130 130 0 0 0 768 60"/>
      <path d="M300 300 Q380 330 460 260" stroke="#8d96d4" stroke-width="6"/>
      <path d="M676 300 Q596 330 516 260" stroke="#8d96d4" stroke-width="6"/>
    </svg>
    <div class="approach-circle c1"><h4>VAMS®</h4><p>Built on a combination of macroeconomic &amp; trends market analysis</p></div>
    <div class="approach-circle c2"><h4>VAQS®</h4><p>Micro &amp; Sentiment VAQS® is designed for stability. Fiscally generated and monthly on a three-year window</p></div>
    <div class="approach-circle c3"><h4>Services</h4><p>VAMS® &amp; VAQS® make Valdmore Capital deliver customized services &amp; solutions</p></div>
  </div>
</section>

<section class="philosophy">
  <div class="wrap">
    <div>
      <div class="eyebrow">Valdmore Investment</div>
      <h2>Advisory Philosophy</h2>
      <ul class="check-list">
        <li><svg width="14" height="12" viewBox="0 0 14 12" fill="none" stroke="#fff" stroke-width="2"><path d="M1 6l4 4 8-9"/></svg>Dynamicly Adaptive to Market Climates</li>
        <li><svg width="14" height="12" viewBox="0 0 14 12" fill="none" stroke="#fff" stroke-width="2"><path d="M1 6l4 4 8-9"/></svg>Attractive Risk Returns with Low Portfolio Turnover</li>
        <li><svg width="14" height="12" viewBox="0 0 14 12" fill="none" stroke="#fff" stroke-width="2"><path d="M1 6l4 4 8-9"/></svg>Europe and U.S. Investment Area</li>
        <li><svg width="14" height="12" viewBox="0 0 14 12" fill="none" stroke="#fff" stroke-width="2"><path d="M1 6l4 4 8-9"/></svg>Built to Follow or Outperform the Market During Upturns and Avoid</li>
        <li><svg width="14" height="12" viewBox="0 0 14 12" fill="none" stroke="#fff" stroke-width="2"><path d="M1 6l4 4 8-9"/></svg>Large Declines During Long – Term Market Turndowns</li>
        <li><svg width="14" height="12" viewBox="0 0 14 12" fill="none" stroke="#fff" stroke-width="2"><path d="M1 6l4 4 8-9"/></svg>Continuously Reviewing, Identifying and Implementing</li>
        <li><svg width="14" height="12" viewBox="0 0 14 12" fill="none" stroke="#fff" stroke-width="2"><path d="M1 6l4 4 8-9"/></svg>Long – Term Investment Strategy</li>
      </ul>
    </div>
    <div class="philosophy-visual">
      <div class="frame"></div>
      <div class="img" role="img" aria-label="Photograph of a tablet showing financial charts on a desk"></div>
    </div>
  </div>
</section>

<section class="strategy">
  <div class="wrap">
    <div class="chart-card">
      <div class="chart-fill" role="img" aria-label="Illustration of two rising performance arrows, one red and one navy"></div>
    </div>
    <div class="strategy-text">
      <div class="eyebrow">Valdmore Capital</div>
      <h2>Investment Strategy</h2>
      <ul class="arrow-list">
        <li><svg width="8" height="10" viewBox="0 0 8 10"><path d="M1 1l6 4-6 4z" fill="var(--navy)"/></svg>Excellent Historic Performance</li>
        <li><svg width="8" height="10" viewBox="0 0 8 10"><path d="M1 1l6 4-6 4z" fill="var(--navy)"/></svg>Value Invest</li>
        <li><svg width="8" height="10" viewBox="0 0 8 10"><path d="M1 1l6 4-6 4z" fill="var(--navy)"/></svg>Active Management</li>
        <li><svg width="8" height="10" viewBox="0 0 8 10"><path d="M1 1l6 4-6 4z" fill="var(--navy)"/></svg>Risk Control</li>
        <li><svg width="8" height="10" viewBox="0 0 8 10"><path d="M1 1l6 4-6 4z" fill="var(--navy)"/></svg>Low Portfolio Turnover</li>
        <li><svg width="8" height="10" viewBox="0 0 8 10"><path d="M1 1l6 4-6 4z" fill="var(--navy)"/></svg>Portfolio Management on clients own account</li>
      </ul>
    </div>
  </div>
</section>

<section class="intelligence">
  <div class="wrap">
    <div class="intel-text">
      <h2>Investment Intelligence</h2>
      <p>Your Exclusive Access to European and American Markets and to the Innovative Investment Approach.</p>
      <p>We attempt to design attractive long term return portfolios, with low portfolio turnover, to better withstand fluctuating markets. Our investment process, VAMS, is built in to allocate to low risk investments during long term market declines and to follow or outperform the market during upturns. Importantly, we understand that investing shouldn't cause you to lose any sleep.</p>
      <span class="btn-solid">Learn More</span>
    </div>
    <div class="phone" role="img" aria-label="Photograph of a smartphone displaying a market chart app"></div>
  </div>
</section>

<section class="message" role="region" aria-label="Contact form over a faded blue city photograph">
  <h2>SEND US A MESSAGE</h2>
  <p class="message-sub">We attempt to design attractive long term return portfolios, with low portfolio turnover, to better withstand</p>
  <div class="contact-form">
    <div class="form-row"><div class="field">Name :</div><div class="field">Surname :</div></div>
    <div class="form-row"><div class="field">Email :</div><div class="field">Phone :</div></div>
    <div class="form-row"><div class="field area">Message :</div></div>
    <span class="btn-send">SEND</span>
  </div>
</section>

<footer class="site-footer">
  <div class="brand"><span class="brand-square"></span>Valdmore Capital</div>
  <ul class="footer-nav"><li>HOME</li><li>PHILOSOPHY</li><li>HOW TO INVEST</li><li>WHAT WE DO</li><li>CONTACT</li><li>INSIGHTS</li></ul>
  <p class="copyright">© Copyrights 2020 - Valdmore Capital All Rights Reserved.</p>
</footer>

</body>
</html>
```